Business card

I have changed logo's and colors. I have uploaded the new logo and colors.

In my head I am thinking about the main logo and text beside logo to be on one side of the card. The other side of the card to have just my picture and contact information.

The "R" emblem and the "equal housing" emblem... cut he MLS from the "R". and remove the wording from the house emblem.

Info on Card:

Lyle Penrose
Designated Broker, CDPE, CNE, GRI
Direct: 602.555.0143
Fax: 623.555.0187
Lyle@PenroseandAssociates.example
www.PenroseandAssociates.example
4153 West Marlow Lane Glendale, AZ 85391

Please see brief as I have uploaded a new logo and a few notes.

Reason: I changed the logo and colors. Please see brief

I am leaning towards maybe a black business card(or at least on the front where the logo is). I liked several designs that were submitted. Please re-submit.

```html
<!DOCTYPE html>
<html lang="en">
<head>
<meta charset="utf-8">
<title>Penrose &amp; Associates — Business Card</title>
<link href="https://fonts.googleapis.com/css2?family=Cinzel:wght@600&family=Arimo:wght@400&display=swap" rel="stylesheet">
<style>
  :root {
    --page: #2b2a2e;
    --card-black: #0b0b0c;
    --teal: #5fa3ad;
    --teal-light: #a9d2d8;
    --orange: #e8651c;
    --orange-deep: #d94f12;
    --orange-glow: #f08a2a;
    --white: #ffffff;
    --ink: #111111;
    --badge-blue: #3a6fc4;
  }
  * { box-sizing: border-box; margin: 0; padding: 0; }
  html, body { width: 1200px; height: 960px; overflow: hidden; }
  body {
    background: var(--page);
    display: flex; align-items: center; justify-content: center;
    font-family: "Arimo", Arial, sans-serif;
  }
  .card {
    position: relative;
    width: 1000px; height: 600px;
    background: var(--card-black);
    overflow: hidden;
  }
  .band-teal {
    position: absolute; left: 0; top: 340px; width: 100%; height: 46px;
    background: var(--teal);
  }
  .band-orange {
    position: absolute; left: 0; top: 386px; width: 100%; height: 214px;
    background: radial-gradient(ellipse at 40% 10%, var(--orange-glow), var(--orange) 45%, var(--orange-deep));
  }
  .brand {
    position: absolute; left: 70px; top: 110px;
    display: flex; align-items: center; gap: 36px;
  }
  .brand-mark {
    width: 170px; height: 170px; border-radius: 50%;
    background: var(--teal);
  }
  .brand-name {
    font-family: "Cinzel", Georgia, serif; font-weight: 600;
    color: var(--teal-light);
    font-size: 52px; line-height: 1.15; letter-spacing: 3px;
  }
  .headshot {
    position: absolute; left: 690px; top: 30px;
    width: 280px; height: 350px;
    border: 6px solid var(--card-black);
    background: linear-gradient(180deg, #f4f1ee 0%, #e9d3c8 45%, #2a2a2c 80%);
  }
  .identity {
    position: absolute; left: 40px; top: 340px; height: 46px;
    display: flex; align-items: center; gap: 16px;
    color: var(--ink);
  }
  .identity .name { font-size: 28px; text-transform: uppercase; letter-spacing: 0.5px; }
  .identity .divider { width: 3px; height: 30px; background: var(--orange); }
  .identity .title { font-size: 19px; }
  .contact {
    position: absolute; left: 40px; top: 400px;
    list-style: none; color: var(--white); font-size: 22px;
  }
  .contact li { display: flex; align-items: center; gap: 14px; height: 36px; }
  .contact .icon { width: 22px; height: 22px; flex: none; }
  .contact .address { padding-left: 36px; }
  .badges {
    position: absolute; left: 720px; top: 440px;
    display: flex; align-items: flex-start; gap: 40px;
  }
  .badge-house { width: 74px; height: 74px; background: var(--ink); border-radius: 6px; }
  .badge-listing {
    width: 120px; height: 64px; background: var(--white);
    border: 4px solid var(--badge-blue);
  }
</style>
</head>
<body>
  <main class="card">
    <div class="band-teal"></div>
    <div class="band-orange"></div>

    <div class="brand">
      <div class="brand-mark"></div>
      <div class="brand-name">Penrose &amp;<br>Associates</div>
    </div>

    <div class="headshot" role="img" aria-label="Portrait photo of the broker in suit and tie"></div>

    <div class="identity">
      <span class="name">Lyle Penrose</span>
      <span class="divider"></span>
      <span class="title">Designated Broker, CDPE, CNE, GRI</span>
    </div>

    <ul class="contact">
      <li class="address">4153 West Marlow Lane Glendale, AZ 85391</li>
      <li>
        <svg class="icon" viewBox="0 0 24 24"><circle cx="12" cy="7" r="5" fill="#111"/><path d="M2 23c0-6 4-9 10-9s10 3 10 9z" fill="#111"/></svg>
        602.555.0143
      </li>
      <li>
        <svg class="icon" viewBox="0 0 24 24"><rect x="6" y="2" width="12" height="7" fill="#111"/><rect x="2" y="10" width="20" height="9" rx="2" fill="#111"/><rect x="6" y="16" width="12" height="6" fill="#fff" stroke="#111" stroke-width="2"/></svg>
        623.555.0187
      </li>
      <li>
        <svg class="icon" viewBox="0 0 24 24"><rect x="1" y="4" width="22" height="16" fill="#111"/><path d="M1 4l11 9 11-9" fill="none" stroke="#fff" stroke-width="2"/></svg>
        Lyle@PenroseandAssociates.example
      </li>
      <li>
        <svg class="icon" viewBox="0 0 24 24"><circle cx="12" cy="12" r="10" fill="#111"/><path d="M2 12h20M12 2c4 4 4 16 0 20M12 2c-4 4-4 16 0 20" fill="none" stroke="#fff" stroke-width="1.5"/></svg>
        www.PenroseandAssociates.example
      </li>
    </ul>

    <div class="badges">
      <div class="badge-house"></div>
      <div class="badge-listing"></div>
    </div>
  </main>
</body>
</html>
```